FernPath....... a dash of Glow

I need a web design for a new business based in London that will be mobile (offered at homes, parks or a local cafe ect) called FernPath. I offer Life Coaching/Counselling sessions, Personal training, Massage and Sports Massage. Sessions range from an hour to half and hour. My aim is to help people along their journey to help give them gain clarity of where there going, helping them to towards their goals, so that can experience bliss. My website should represent a place people can come to release their stress and worries so that they leave feeling lighter, clearer and happier. I would like my website to reflect someone feeling ALIVE. I would also like a logo design for FernPath with a sentence underneath or near saying A Dash of Glow.

Target Market(s)

middle class people

Industry/Entity Type

Business

Coding

Coded - Design and coding required

Number of Pages Required

4 page

Requirements
Must have
• 1st page About us
• 2nd page Services
• 3rd page Prices
• 4th page contact details
Nice to have
• mixture of cultures in images

```html
<!DOCTYPE html>
<html lang="en">
<head>
<meta charset="utf-8">
<title>FernPath — A Dash of Glow</title>
<link rel="stylesheet" href="https://fonts.googleapis.com/css2?family=Raleway:wght@400;500;600;700&family=Open+Sans:wght@400;600;700&display=swap">
<style>
:root{
  --teal:#3dbfa3;
  --teal-deep:#2fae94;
  --yellow:#f8e73a;
  --ink:#1e1e1e;
  --grey:#6f6f6f;
  --white:#ffffff;
  --cream:#fffaf0;
}
*{margin:0;padding:0;box-sizing:border-box}
html,body{width:1200px;height:2521px;overflow:hidden;background:var(--white)}
body{position:relative;font-family:'Open Sans',sans-serif;color:var(--ink)}
.abs{position:absolute}

/* header */
.topbar{left:0;top:0;width:1200px;height:47px}
.topbar-social{top:13px;left:486px;display:flex;gap:24px}
.topbar-social span{width:14px;height:14px;border-radius:50%;background:var(--white);opacity:.9}
.topbar-item{top:12px;color:var(--white);font-size:16px;display:flex;align-items:center;gap:10px;white-space:nowrap}
.topbar-item.mail{left:656px}
.topbar-item.phone{left:936px;font-size:18px;font-weight:600}
.brand{left:94px;top:18px;width:190px;text-align:center}
.brand-mark{width:40px;height:40px;border-radius:50%;background:var(--yellow);margin:0 auto 8px}
.brand-name{font-family:'Raleway',sans-serif;font-size:26px;font-weight:600;color:#555;letter-spacing:1px;line-height:1;white-space:nowrap}
.brand-tag{font-family:'Raleway',sans-serif;font-size:14px;color:#555;margin-top:4px;white-space:nowrap}
.nav{top:88px;left:0;width:1200px;height:20px}
.nav a{position:absolute;font-family:'Raleway',sans-serif;font-size:14px;font-weight:500;color:var(--ink);text-decoration:none;letter-spacing:.3px;white-space:nowrap}

/* hero */
.hero{left:0;top:143px;width:1200px;height:592px;background:
  radial-gradient(ellipse 300px 280px at 900px 330px,#fffdf2 0%,#fff2c4 30%,rgba(255,225,150,0) 80%),
  radial-gradient(ellipse 900px 220px at 600px 560px,rgba(170,110,40,.55) 0%,rgba(170,110,40,0) 80%),
  linear-gradient(180deg,#efe0c2 0%,#f3d08e 45%,#f1b95a 72%,#d7923f 88%,#8f5b2c 100%)}
.hero-silhouette{left:690px;top:150px;width:360px;height:585px;background:radial-gradient(ellipse 120px 300px at 50% 60%,rgba(60,35,20,.35) 0%,rgba(60,35,20,0) 80%)}
.hero-title{left:148px;top:384px;font-family:'Raleway',sans-serif;color:#333;line-height:1}
.hero-title .small{font-size:33px;font-weight:500;display:block;letter-spacing:.5px}
.hero-title .big{font-size:84px;font-weight:400;color:var(--teal);display:block;margin-top:4px;letter-spacing:1px}
.hero-dots{left:528px;top:696px;display:flex;gap:20px}
.hero-dots span{width:13px;height:13px;border-radius:50%;border:2px solid #444}
.hero-dots span.on{background:var(--teal);border-color:var(--teal)}

/* services */
.section-title{left:0;width:1200px;text-align:center;font-family:'Raleway',sans-serif;font-weight:700;font-size:29px;color:var(--ink);letter-spacing:.5px}
.section-title em{font-style:normal;color:var(--teal)}
.services-sub{left:0;top:832px;width:1200px;text-align:center;font-size:13px;color:#555}
.service{top:908px;width:300px;text-align:center}
.service-photo{width:200px;height:200px;border-radius:50%;border:4px solid var(--yellow);margin:0 auto}
.service-name{margin-top:42px;font-family:'Raleway',sans-serif;font-size:15px;font-weight:500;letter-spacing:.3px;white-space:nowrap}

/* about band */
.about{left:0;top:1237px;width:1200px;height:489px;background:linear-gradient(180deg,var(--teal) 0%,#4ec4aa 100%)}
.about-figure{left:620px;top:1250px;width:420px;height:476px;background:radial-gradient(ellipse 160px 240px at 50% 65%,rgba(255,255,255,.16) 0%,rgba(255,255,255,0) 80%)}
.about-mark{left:578px;top:1290px;width:44px;height:44px;border-radius:50%;background:var(--yellow)}
.about-name{left:0;top:1372px;width:1200px;text-align:center;font-family:'Raleway',sans-serif;font-size:34px;font-weight:700;color:var(--white);letter-spacing:.5px}
.about-text{left:84px;top:1434px;width:1032px;text-align:center;color:var(--white);font-size:13px;line-height:24px}
.about-text p+p{margin-top:24px}
.btn{left:518px;top:1627px;width:164px;height:44px;border-radius:22px;background:var(--yellow);color:var(--ink);font-family:'Raleway',sans-serif;font-weight:600;font-size:15px;display:flex;align-items:center;justify-content:center;gap:8px}

/* blog */
.blog{left:0;top:1726px;width:1200px;height:551px;background:linear-gradient(180deg,var(--cream) 0%,#fdf3f0 100%)}
.post{top:1852px;width:323px}
.post-photo{width:323px;height:227px;position:relative}
.post-date{position:absolute;left:67px;bottom:0;width:190px;height:40px;border-radius:14px 14px 0 0;background:var(--yellow);display:flex;align-items:center;justify-content:center;gap:6px;font-family:'Raleway',sans-serif;white-space:nowrap}
.post-date b{font-size:20px;font-weight:700}
.post-date span{font-size:14px;font-weight:500}
.post-title{margin-top:30px;font-family:'Raleway',sans-serif;font-size:16px;font-weight:600;letter-spacing:.2px;white-space:nowrap}
.post-excerpt{margin-top:18px;font-size:13px;line-height:26px;color:var(--grey)}

/* footer */
.footer-band{left:0;top:2277px;width:1200px;height:244px;background:var(--teal)}
.footer-box{left:79px;top:2244px;width:1040px;height:218px;background:var(--yellow);box-shadow:0 4px 10px rgba(0,0,0,.15)}
.footer-heading{top:2297px;font-family:'Raleway',sans-serif;font-weight:600;font-size:16px;color:var(--teal-deep);display:flex;align-items:center;gap:8px;letter-spacing:.3px;white-space:nowrap}
.hours{left:112px;top:2326px;font-size:17px}
.hours div{display:flex;align-items:center;height:25px;white-space:nowrap}
.hours small{width:64px;text-align:right;font-size:11px;font-weight:600;margin-right:22px;white-space:nowrap}
.foot-brand{left:490px;top:2268px;width:220px;text-align:center}
.foot-social{left:527px;top:2399px;display:flex;gap:14px}
.foot-social span{width:38px;height:38px;border-radius:50%;border:2px solid var(--teal-deep);display:flex;align-items:center;justify-content:center}
.foot-social span::after{content:"";width:8px;height:8px;border-radius:50%;background:var(--teal-deep)}
.contact-list{left:806px;top:2334px}
.contact-list div{display:flex;align-items:center;height:32px;white-space:nowrap}
.contact-list small{width:68px;font-size:11px;font-weight:600;text-align:right;margin-right:12px;white-space:nowrap}
.contact-list .call{font-size:22px;font-weight:700}
.contact-list .mail{font-size:17px;font-weight:700}
.copyright{left:0;top:2482px;width:1200px;text-align:center;color:var(--white);font-size:13px}
.copyright b{color:var(--yellow)}
</style>
</head>
<body>

<header>
  <svg class="abs topbar" viewBox="0 0 1200 47" width="1200" height="47" aria-hidden="true">
    <path d="M328 0 H1200 V47 H440 C395 47 355 25 328 0 Z" fill="#3dbfa3"/>
    <line x1="630" y1="8" x2="630" y2="40" stroke="#ffffff" stroke-opacity=".4"/>
    <line x1="888" y1="8" x2="888" y2="40" stroke="#ffffff" stroke-opacity=".4"/>
  </svg>
  <div class="abs topbar-social"><span></span><span></span><span></span></div>
  <div class="abs topbar-item mail">
    <svg width="16" height="12" viewBox="0 0 16 12"><rect width="16" height="12" rx="1" fill="#fff"/><path d="M0 1 L8 7 L16 1" stroke="#3dbfa3" stroke-width="1.5" fill="none"/></svg>
    hello@fernpath.co.uk
  </div>
  <div class="abs topbar-item phone">
    <svg width="16" height="16" viewBox="0 0 24 24"><path fill="#fff" d="M6.6 10.8a15.1 15.1 0 0 0 6.6 6.6l2.2-2.2a1 1 0 0 1 1-.25 11.4 11.4 0 0 0 3.6.6 1 1 0 0 1 1 1V20a1 1 0 0 1-1 1A17 17 0 0 1 3 4a1 1 0 0 1 1-1h3.5a1 1 0 0 1 1 1 11.4 11.4 0 0 0 .6 3.6 1 1 0 0 1-.25 1z"/></svg>
    (800) 555-0142
  </div>
  <div class="abs brand">
    <div class="brand-mark"></div>
    <div class="brand-name">FERNPATH</div>
    <div class="brand-tag">A Dash of Glow</div>
  </div>
  <nav class="abs nav">
    <a style="left:378px">HOME</a>
    <a style="left:474px">ABOUT</a>
    <a style="left:576px">SERVICES</a>
    <a style="left:696px">CLASSES</a>
    <a style="left:810px">TESTIMONIALS</a>
    <a style="left:962px">BLOG</a>
    <a style="left:1054px">CONTACT</a>
  </nav>
</header>

<section class="abs hero" role="img" aria-label="Photo of a woman with arms raised against a golden sunset sky"></section>
<div class="abs hero-silhouette" aria-hidden="true"></div>
<h1 class="abs hero-title"><span class="small">A DASH OF</span><span class="big">GLOW</span></h1>
<div class="abs hero-dots"><span></span><span></span><span class="on"></span><span></span><span></span></div>

<h2 class="abs section-title" style="top:782px">OUR <em>SERVICES</em></h2>
<p class="abs services-sub">A wonderful sereny has taken possession of soul, like these sweet mornings of idma aute rure dolor in reprehendet</p>
<div class="abs service" style="left:97px">
  <div class="service-photo" role="img" aria-label="Photo of a counselling conversation in a bright room" style="background:radial-gradient(circle at 45% 40%,#c98f86 0%,#a86f78 35%,rgba(168,111,120,0) 70%),linear-gradient(135deg,#f6f1e8,#e7d6c8 55%,#b4a0a8)"></div>
  <div class="service-name">COUNSELLING SESSIONS</div>
</div>
<div class="abs service" style="left:445px">
  <div class="service-photo" role="img" aria-label="Photo of a group stretching in a training studio" style="background:radial-gradient(circle at 40% 55%,#c7a8cc 0%,rgba(199,168,204,0) 45%),radial-gradient(circle at 70% 55%,#a9d0cc 0%,rgba(169,208,204,0) 40%),linear-gradient(180deg,#f3f5f6,#e2e6e8 60%,#6a7476)"></div>
  <div class="service-name">PERSONAL TRAINING</div>
</div>
<div class="abs service" style="left:793px">
  <div class="service-photo" role="img" aria-label="Photo of a relaxing massage setting with plants and stones" style="background:radial-gradient(circle at 60% 45%,#d7a88a 0%,rgba(215,168,138,0) 45%),linear-gradient(180deg,#a9cf6e 0%,#c5d58f 45%,#b7a27a 75%,#7c6b4a)"></div>
  <div class="service-name">MASSAGE AND SPORTS MASSAGE</div>
</div>

<section class="abs about"></section>
<div class="abs about-figure" role="img" aria-label="Faint photo of a person raising both arms"></div>
<div class="abs about-mark"></div>
<div class="abs about-name">FERNPATH</div>
<div class="abs about-text">
  <p>Lorem ipsum dolor sit amet, consectetur adipiscing elit. Cras sollicitudin diam urna, at feugiat ante consectetur vitae. Aenean fringilla porttitor rutrum. Cras id egestas quam. Sed placerat mauris facilisis nunc placerat, at molestie enim dignissim. Donec at aliquet dolor. Morbi quis mollis lectus, id mattis eros. Sed urna arcu,</p>
  <p>ultricies ut diam iaculis, iaculis pulvinar tellus. Quisque dapibus ut sapien in varius. In ullamcorper et nisi ac consectetur. Suspendisse id felis eget urna condimentum consequat non eu nulla. Integer vehicula leo nulla, lobortis gravida lorem tincidunt vitae. Duis dapibus tincidunt lorem, vitae dignissim libero molestie at. Aenean gravida lectus odio, sit amet sodales neque laoreet id. Proin blandit ultrices consectetur. Vestibulum efficitur imperdiet tempus. Ut ornare massa porttitor fermentum suscipit.</p>
</div>
<div class="abs btn">Read More
  <svg width="12" height="12" viewBox="0 0 12 12"><circle cx="6" cy="6" r="6" fill="#1e1e1e"/><path d="M5 3.5 L7.5 6 L5 8.5" stroke="#f8e73a" stroke-width="1.6" fill="none"/></svg>
</div>

<section class="abs blog"></section>
<h2 class="abs section-title" style="top:1779px;font-size:27px">RECENT FROM <em>BLOG</em></h2>
<article class="abs post" style="left:79px">
  <div class="post-photo" role="img" aria-label="Photo of a smiling woman leaning on an exercise ball in a class" style="background:radial-gradient(ellipse 110px 90px at 50% 45%,#f2d2b8 0%,rgba(242,210,184,0) 80%),linear-gradient(180deg,#b9c9da 0%,#d7c3b2 45%,#3a7cc4 75%,#1f5aa3)">
    <div class="post-date"><b>07</b><span>OCTOBER 2015</span></div>
  </div>
  <h3 class="post-title">PREGNANT YOGA EXERCISES IN 30MIN</h3>
  <p class="post-excerpt">A wonderful sereny has taken possession of my entire soul, like these sweet mornings of spring.</p>
</article>
<article class="abs post" style="left:439px">
  <div class="post-photo" role="img" aria-label="Photo of women doing side stretches in a bright studio" style="background:radial-gradient(ellipse 70px 110px at 30% 60%,#e2a9c8 0%,rgba(226,169,200,0) 80%),radial-gradient(ellipse 70px 110px at 55% 55%,#c9aed0 0%,rgba(201,174,208,0) 80%),radial-gradient(ellipse 70px 100px at 82% 60%,#b5d8cf 0%,rgba(181,216,207,0) 80%),linear-gradient(180deg,#f4f6f7,#e6e9ea 70%,#8a9294)">
    <div class="post-date"><b>29</b><span>AUGUST 2015</span></div>
  </div>
  <h3 class="post-title">PREGNANT YOGA EXERCISES IN 30MIN</h3>
  <p class="post-excerpt">A wonderful sereny has taken possession of my entire soul, like these sweet mornings of spring.</p>
</article>
<article class="abs post" style="left:797px">
  <div class="post-photo" role="img" aria-label="Photo of two women stretching beside a blue exercise ball" style="background:radial-gradient(circle at 80% 50%,#4f86d0 0%,#3a6fbf 20%,rgba(58,111,191,0) 32%),radial-gradient(ellipse 120px 90px at 35% 55%,#f1e6dc 0%,rgba(241,230,220,0) 80%),linear-gradient(180deg,#d9d0c6,#e4dace 60%,#b79f7d)">
    <div class="post-date"><b>15</b><span>MARCH 2015</span></div>
  </div>
  <h3 class="post-title">PREGNANT YOGA EXERCISES IN 30MIN</h3>
  <p class="post-excerpt">A wonderful sereny has taken possession of my entire soul, like these sweet mornings of spring.</p>
</article>

<footer>
  <div class="abs footer-band"></div>
  <svg class="abs" style="left:64px;top:2244px" width="1072" height="33" viewBox="0 0 1072 33" aria-hidden="true">
    <path d="M15 0 L15 33 L0 33 Z" fill="#2a9f86"/>
    <path d="M1055 0 L1072 33 L1055 33 Z" fill="#2a9f86"/>
  </svg>
  <div class="abs footer-box"></div>

  <div class="abs footer-heading" style="left:121px">
    <svg width="16" height="16" viewBox="0 0 16 16"><circle cx="8" cy="8" r="6.5" fill="none" stroke="#2fae94" stroke-width="1.8"/><path d="M8 4 V8 L10.5 9.5" stroke="#2fae94" stroke-width="1.8" fill="none"/></svg>
    TIMING
  </div>
  <div class="abs hours">
    <div><small>MON-FRI :</small>6:00am - 11:00pm</div>
    <div><small>SAT :</small>7:00am - 10:00pm</div>
    <div><small>SUN :</small>Closed</div>
  </div>

  <div class="abs foot-brand">
    <div class="brand-mark" style="width:36px;height:36px;background:#f4a53a;margin-bottom:10px"></div>
    <div class="brand-name" style="font-size:24px">FERNPATH</div>
    <div class="brand-tag">A Dash of Glow</div>
  </div>
  <div class="abs foot-social"><span></span><span></span><span></span></div>

  <div class="abs footer-heading" style="left:824px">
    <svg width="16" height="16" viewBox="0 0 24 24"><path fill="#2fae94" d="M6.6 10.8a15.1 15.1 0 0 0 6.6 6.6l2.2-2.2a1 1 0 0 1 1-.25 11.4 11.4 0 0 0 3.6.6 1 1 0 0 1 1 1V20a1 1 0 0 1-1 1A17 17 0 0 1 3 4a1 1 0 0 1 1-1h3.5a1 1 0 0 1 1 1 11.4 11.4 0 0 0 .6 3.6 1 1 0 0 1-.25 1z"/></svg>
    JOIN US / CONTACT US
  </div>
  <div class="abs contact-list">
    <div><small>CALL US :</small><span class="call">(800) 555-0147</span></div>
    <div><small>EMAIL US :</small><span class="mail">hello@fernpath.co.uk</span></div>
  </div>

  <p class="abs copyright">Copyright © <b>FERNPATH.</b> &nbsp;| &nbsp;All Rights Reserved</p>
</footer>

</body>
</html>
```